Business Card for Canvas Lotus-Eco Friendly Organic Clothing Brand

We are looking for an amazing business card for our eco friendly, organic clothing brand. We are thinking maybe a business card with a peel off sticker on the back, since our hanging clothing tag is a peel off sticker on the back. I will attach our hang tag so we can make sure we stay in line with our design. I've also attached a bag we are doing because I do like the scattered emblem look as well.

```html
<!DOCTYPE html>
<html lang="en">
<head>
<meta charset="utf-8">
<title>Canvas Lotus – Business Card</title>
<link rel="stylesheet" href="https://fonts.googleapis.com/css2?family=Didact+Gothic&display=swap">
<style>
  :root {
    --bg: #e9e6e1;
    --card-white: #ffffff;
    --card-black: #121212;
    --panel: #151515;
    --gold: #d8ad2e;
    --gold-light: #f3d676;
    --text-light: #f2f2f2;
    --dot: #cfcfcf;
    --camo-a: #8a7a3a;
    --camo-b: #d9c27a;
    --camo-c: #4f4a2a;
  }
  * { box-sizing: border-box; margin: 0; padding: 0; }
  html, body { width: 1200px; height: 950px; overflow: hidden; }
  body {
    background: var(--bg);
    font-family: "Didact Gothic", "Century Gothic", sans-serif;
    position: relative;
  }
  .card {
    position: absolute;
    left: 220px;
    width: 760px;
    height: 420px;
    border-radius: 6px;
    box-shadow: 0 6px 20px rgba(0,0,0,0.18);
    overflow: hidden;
  }
  .card--front { top: 35px; background: var(--card-white); }
  .card--back { top: 495px; background: var(--card-black); }

  .brand-name {
    color: var(--gold);
    font-weight: 400;
    letter-spacing: 1px;
    white-space: nowrap;
  }
  .card--front .brand-name {
    position: absolute;
    top: 62px;
    left: 0;
    width: 100%;
    text-align: center;
    font-size: 44px;
  }

  .info-panel {
    position: absolute;
    left: 110px;
    top: 165px;
    width: 570px;
    height: 210px;
    background: var(--panel);
    border: 3px solid var(--gold);
    border-radius: 14px;
    box-shadow: inset 0 0 0 3px var(--panel), inset 0 0 0 4px #3a3a3a;
  }
  .info-panel__dot {
    position: absolute;
    right: 18px;
    bottom: 26px;
    width: 10px;
    height: 10px;
    border-radius: 50%;
    background: var(--dot);
  }

  .emblem-frame {
    position: absolute;
    background: var(--panel);
    border: 3px solid var(--gold);
    transform: rotate(-14deg);
    display: flex;
    align-items: center;
    justify-content: center;
  }
  .card--front .emblem-frame { left: 45px; top: 120px; width: 170px; height: 170px; }
  .emblem-figure {
    width: 62%;
    height: 70%;
    border-radius: 40% 40% 20% 20%;
    background: radial-gradient(circle at 40% 40%, var(--camo-b), var(--camo-a) 55%, var(--camo-c));
  }

  .contact {
    position: absolute;
    left: 300px;
    top: 195px;
    color: var(--text-light);
    font-size: 17px;
    line-height: 1.45;
  }
  .contact__name { color: var(--gold); font-size: 22px; }
  .contact__role { color: var(--text-light); font-size: 17px; margin-left: 10px; }
  .contact__label { color: var(--gold); }

  .back-pattern {
    position: absolute;
    inset: 0;
    background: radial-gradient(ellipse at 50% 45%, #262626, var(--card-black) 75%);
  }
  .brand-tag {
    position: absolute;
    left: 250px;
    top: 145px;
    width: 340px;
    height: 120px;
    border: 3px solid var(--gold);
    border-radius: 12px;
    background: rgba(20,20,20,0.9);
    text-align: right;
    padding: 26px 30px 0 0;
  }
  .brand-tag .brand-name { font-size: 32px; }
  .brand-tag__web { color: var(--text-light); font-size: 13px; margin-top: 10px; }
  .card--back .emblem-frame { left: 190px; top: 160px; width: 110px; height: 110px; }
</style>
</head>
<body>
  <section class="card card--front">
    <div class="brand-name">Canvas Lotus</div>
    <div class="info-panel"><span class="info-panel__dot"></span></div>
    <div class="emblem-frame">
      <div class="emblem-figure" role="img" aria-label="Camouflage-patterned seated meditation figure"></div>
    </div>
    <div class="contact">
      <div><span class="contact__name">Sam Rivera</span><span class="contact__role">– President</span></div>
      <div>2710 Alder Lane</div>
      <div>Brook Hollow, NY 11210</div>
      <div><span class="contact__label">P:</span> 514 2290 6371 <span class="contact__label">M:</span> 847 1936 4402</div>
      <div><span class="contact__label">F:</span> 833 5017 2689 <span class="contact__label">E:</span> info@canvaslotus.com</div>
    </div>
  </section>

  <section class="card card--back">
    <div class="back-pattern" role="img" aria-label="Faint scattered pattern of peace words, hearts and peace symbols"></div>
    <div class="brand-tag">
      <div class="brand-name">Canvas Lotus</div>
      <div class="brand-tag__web">www.canvaslotus.com</div>
    </div>
    <div class="emblem-frame">
      <div class="emblem-figure" role="img" aria-label="Camouflage-patterned seated meditation figure"></div>
    </div>
  </section>
</body>
</html>
```